Business Card design for law firm = Brightvale Australia

We are seeking a new design for our business cards.
We are keeping our logo, which is attached.
We need space for
Name
Title
Address is , which is
Level 7
214 Marlowe Street
Sydney NSW 2047
Phone :
Mobile :
Fax :
Email :
DX :
website www.brightvale-example.com.au

Industry/Entity Type

Law Firm / Banking and Finance

Contact Information for Business Card

We are seeking a new design for our business cards. We are keeping our logo. We need space for Name Title Address is Level 7 214 Marlowe Street Sydney NSW 2047 Phone Mobile Fax Email DX website www.brightvale-example.com.au

Colors
0054AA
0677BA
7BADD7
CADEEF
E8F1F8

Requirements
Must have
• see our website for general feel www.brightvale-example.com.au

```html
<!DOCTYPE html>
<html lang="en">
<head>
<meta charset="utf-8">
<title>Brightvale Australia — Business Cards</title>
<link rel="stylesheet" href="https://fonts.googleapis.com/css2?family=EB+Garamond:wght@400&family=Open+Sans:wght@400&display=swap">
<style>
  :root {
    --backdrop: #2c2c2d;
    --card-dark: #1c1d1f;
    --card-light: #2f3034;
    --brand-blue: #2f4e9e;
    --brand-cyan: #1a8fc6;
    --text-light: #d9d9d9;
    --icon-cut: #232427;
    --serif: "EB Garamond", Georgia, serif;
    --sans: "Open Sans", Arial, sans-serif;
  }
  html, body {
    margin: 0;
    padding: 0;
    width: 1200px;
    height: 1138px;
    overflow: hidden;
    background: var(--backdrop);
  }
  .stage { position: relative; width: 1200px; height: 1138px; }

  .card {
    position: absolute;
    width: 620px;
    height: 376px;
    border-radius: 16px;
    background: linear-gradient(160deg, var(--card-dark) 0%, #232427 55%, var(--card-light) 100%);
    box-shadow: 0 6px 14px rgba(0,0,0,0.45);
    overflow: hidden;
  }
  .card--front { left: 272px; top: 184px; }
  .card--back  { left: 274px; top: 606px; }

  .brand-name {
    position: absolute;
    margin: 0;
    font-family: var(--serif);
    font-weight: 400;
    color: var(--brand-blue);
    line-height: 1;
    white-space: nowrap;
  }
  .tagline {
    position: absolute;
    margin: 0;
    font-family: var(--sans);
    font-weight: 400;
    color: var(--brand-cyan);
    line-height: 1;
    white-space: nowrap;
  }

  /* Front */
  .card--front .brand-name { left: 0; width: 620px; text-align: center; top: 150px; font-size: 52px; }
  .card--front .tagline { left: 0; width: 620px; text-align: center; top: 222px; font-size: 18px; letter-spacing: 2px; }
  .website-line {
    position: absolute;
    left: 0; width: 620px; top: 336px;
    text-align: center;
    font-family: var(--serif);
    font-size: 14px;
    letter-spacing: 5.5px;
    color: var(--text-light);
    white-space: nowrap;
  }
  .accent-bar {
    position: absolute;
    left: 142px; width: 340px; bottom: 0; height: 8px;
    background: var(--brand-blue);
  }

  /* Back */
  .card--back .brand-name { left: 40px; top: 110px; font-size: 40px; }
  .card--back .tagline { left: 40px; top: 166px; font-size: 14px; letter-spacing: 1.2px; }

  .person {
    position: absolute; left: 40px; top: 238px;
    font-family: var(--serif); white-space: nowrap;
  }
  .person-name { font-size: 24px; color: var(--brand-blue); margin-right: 12px; }
  .person-title { font-size: 17px; color: var(--text-light); }

  .contact {
    position: absolute; left: 40px; top: 278px;
    font-family: var(--serif); font-size: 16.5px; color: var(--text-light);
  }
  .contact-row { display: flex; height: 22.5px; align-items: center; white-space: nowrap; }
  .contact-item { display: flex; align-items: center; }
  .contact-item--first { width: 160px; }
  .icon { width: 14px; height: 14px; margin-right: 12px; fill: var(--brand-cyan); flex: none; }
  .address span { margin-right: 8px; }
</style>
</head>
<body>
<div class="stage">

  <section class="card card--front" aria-label="Card front">
    <h1 class="brand-name">Brightvale</h1>
    <p class="tagline">clear counsel for finance</p>
    <div class="website-line">www.brightvale-example.com.au</div>
    <div class="accent-bar"></div>
  </section>

  <section class="card card--back" aria-label="Card back">
    <h2 class="brand-name">Brightvale</h2>
    <p class="tagline">clear counsel for finance</p>

    <div class="person">
      <span class="person-name">Sam Whitlock</span>
      <span class="person-title">Managing Director</span>
    </div>

    <div class="contact">
      <div class="contact-row">
        <div class="contact-item contact-item--first">
          <svg class="icon" viewBox="0 0 16 16" aria-hidden="true"><path d="M2 5c0-2 3-3 6-3s6 1 6 3v1h-3V5H5v1H2z"/><path d="M4 7h8l2 6H2z"/></svg>
          02 9000 0142
        </div>
        <div class="contact-item">
          <svg class="icon" viewBox="0 0 16 16" aria-hidden="true"><path d="M1 3h14v10H1z"/><path d="M1 3l7 6 7-6" fill="none" stroke="var(--icon-cut)" stroke-width="1.4"/></svg>
          sam.whitlock@brightvale-example.com.au
        </div>
      </div>
      <div class="contact-row">
        <div class="contact-item contact-item--first">
          <svg class="icon" viewBox="0 0 16 16" aria-hidden="true"><path d="M4 1h8v4H4z"/><path d="M1 6h14v6h-3v3H4v-3H1z"/><path d="M5.5 10h5v3.5h-5z" fill="var(--icon-cut)"/></svg>
          02 9000 0187
        </div>
        <div class="contact-item">
          <svg class="icon" viewBox="0 0 16 16" aria-hidden="true"><circle cx="8" cy="8" r="7"/><path d="M1 8h14M8 1c-3 3.5-3 10.5 0 14M8 1c3 3.5 3 10.5 0 14" fill="none" stroke="var(--icon-cut)" stroke-width="1"/></svg>
          https://www.brightvale-example.com.au
        </div>
      </div>
      <div class="contact-row address">
        <svg class="icon" viewBox="0 0 16 16" aria-hidden="true"><path d="M8 1a5 5 0 0 1 5 5c0 4-5 9-5 9S3 10 3 6a5 5 0 0 1 5-5z"/><circle cx="8" cy="6" r="2" fill="var(--icon-cut)"/></svg>
        <span>Level 7</span><span>214 Marlowe Street</span><span>Sydney NSW 2047</span>
      </div>
    </div>
  </section>

</div>
</body>
</html>
```